Kettleby Twins Playing Cards

We are wanting a cool design for a playing card that includes our logo(s). I will attach our two logos, we are open to using either one of them or another version of them. I will also attach some pictures of card decks to use for inspiration. These are just decks that we have seen from other artists that we liked. We are located in West Texas so although not necessary, a Sotol or Agave or cactus or quail (bird) or some sort of sunset would pay homage to our surroundings. I realize the examples are all very different, but those are just some decks that we like! Thank you!

```html
<!DOCTYPE html>
<html lang="en">
<head>
<meta charset="utf-8">
<title>Kettleby Twins Playing Cards</title>
<link href="https://fonts.googleapis.com/css2?family=Rye&display=swap" rel="stylesheet">
<style>
  :root {
    --stage: #222222;
    --card-black: #060708;
    --gold-light: #f3d892;
    --gold: #d4a53c;
    --gold-mid: #c08d2c;
    --gold-deep: #8a6216;
    --band-black: #0b0b0b;
  }
  * { margin: 0; padding: 0; box-sizing: border-box; }
  html, body { width: 1200px; height: 900px; overflow: hidden; background: var(--stage); }
  .canvas { position: relative; width: 1200px; height: 900px; background: var(--stage); }

  .card {
    position: absolute;
    top: 198px;
    width: 360px;
    height: 504px;
    border-radius: 24px;
    background: var(--card-black);
  }
  .card-back { left: 190px; }
  .card-face { left: 650px; }

  .gold-rule {
    position: absolute;
    inset: 12px;
    border: 4px solid var(--gold);
    border-radius: 16px;
  }
  .gold-rule--inner {
    inset: 24px;
    border-width: 2px;
    border-radius: 10px;
  }

  .back-pattern {
    position: absolute;
    inset: 24px;
    border-radius: 10px;
    overflow: hidden;
    background:
      radial-gradient(ellipse at 50% 50%, rgba(243,216,146,0.55) 0%, rgba(243,216,146,0) 60%),
      linear-gradient(160deg, var(--gold-mid) 0%, var(--gold) 30%, #e2bc62 50%, var(--gold) 70%, var(--gold-mid) 100%);
  }
  .back-frame {
    position: absolute;
    inset: 10px;
    border: 1.5px solid var(--card-black);
    border-radius: 6px;
  }
  .back-diamond {
    position: absolute;
    left: 50%;
    top: 50%;
    width: 210px;
    height: 210px;
    transform: translate(-50%, -50%) rotate(45deg);
    border: 2px solid var(--card-black);
  }

  .brand-band {
    position: absolute;
    left: 50%;
    top: 50%;
    transform: translate(-50%, -50%);
    display: flex;
    align-items: center;
    gap: 12px;
    padding: 14px 22px;
    background: var(--band-black);
    border: 3px solid var(--gold);
    border-radius: 10px;
  }
  .brand-mark {
    width: 20px;
    height: 20px;
    border-radius: 50%;
    background: var(--gold);
    flex: none;
  }
  .brand-name {
    font-family: "Rye", serif;
    font-size: 25px;
    line-height: 1;
    color: var(--gold-light);
    white-space: nowrap;
  }

  .corner-index {
    position: absolute;
    display: flex;
    flex-direction: column;
    align-items: center;
    gap: 2px;
    color: var(--gold-light);
  }
  .corner-index--top { top: 40px; left: 42px; }
  .corner-index--bottom { bottom: 40px; right: 42px; transform: rotate(180deg); }
  .rank {
    font-family: "Rye", serif;
    font-size: 44px;
    line-height: 1;
  }
  .suit-pip { width: 30px; height: 32px; }

  .ace-spade {
    position: absolute;
    left: 50%;
    top: 50%;
    width: 190px;
    height: 210px;
    transform: translate(-50%, -50%);
  }
</style>
</head>
<body>
<main class="canvas">
  <svg width="0" height="0" aria-hidden="true" style="position:absolute">
    <defs>
      <linearGradient id="goldFoil" x1="0" y1="0" x2="1" y2="1">
        <stop offset="0" stop-color="#f3d892"/>
        <stop offset="0.5" stop-color="#d4a53c"/>
        <stop offset="1" stop-color="#a97a22"/>
      </linearGradient>
      <path id="spadeShape" d="M50 2 C35 25 4 40 4 66 C4 84 20 94 35 90 C42 88 46 84 48 80 C47 92 42 100 30 106 L70 106 C58 100 53 92 52 80 C54 84 58 88 65 90 C80 94 96 84 96 66 C96 40 65 25 50 2 Z"/>
    </defs>
  </svg>

  <section class="card card-back" aria-label="Card back">
    <div class="gold-rule"></div>
    <div class="back-pattern" role="img" aria-label="Gold and black paisley and floral ornament pattern covering the card back">
      <div class="back-frame"></div>
      <div class="back-diamond"></div>
    </div>
    <div class="brand-band">
      <span class="brand-mark"></span>
      <span class="brand-name">Kettleby Twins</span>
    </div>
  </section>

  <section class="card card-face" aria-label="Ace of spades">
    <div class="gold-rule"></div>
    <div class="gold-rule gold-rule--inner"></div>

    <div class="corner-index corner-index--top">
      <span class="rank">A</span>
      <svg class="suit-pip" viewBox="0 0 100 108" aria-hidden="true"><use href="#spadeShape" fill="url(#goldFoil)"/></svg>
    </div>

    <svg class="ace-spade" viewBox="0 0 100 108" role="img" aria-label="Large gold spade filled with paisley and floral ornament">
      <use href="#spadeShape" fill="url(#goldFoil)"/>
    </svg>

    <div class="corner-index corner-index--bottom">
      <span class="rank">A</span>
      <svg class="suit-pip" viewBox="0 0 100 108" aria-hidden="true"><use href="#spadeShape" fill="url(#goldFoil)"/></svg>
    </div>
  </section>
</main>
</body>
</html>
```